Web Calculator design Housing Investment

We have a web calculator that needs to be fixed from a design perspective. The key tasks are:<br/>1. Selecting icons / pictures / colours for the various steps<br/>2. Designing navigation between calculator steps<br/>3. Making suggestions for chart design. The limitation is that the charts are all using the Vextra API (the same charts that Vextra Grids use).<br/><br/>There are four entry screens and then a result screen. See attached PDF for screenshots. You can see our website at https://larkhollowfunds.com for our corporate colours and style.

Target Market(s)

Real Estate Investors

Industry/Entity Type

Financial Planning

Number of Pages Required

1 page

Font styles to use
Sans Serif
Other font styles liked:
• Ubuntu

Colors
86cae7
3176b5
0455a3
ffffff

Requirements
Must have
• New Icons
• Suggested design for navigation
• Suggested design for charts

```html
<!DOCTYPE html>
<html lang="en">
<head>
<meta charset="utf-8">
<title>Housing Investment Calculator – Screen Designs</title>
<link rel="stylesheet" href="https://fonts.googleapis.com/css2?family=Montserrat:wght@400;500;600;700&display=swap">
<style>
:root{
  --stage:#7f7f7f;
  --brand:#1a8cff;
  --brand-deep:#0a66ff;
  --brand-light:#86bdf7;
  --teal:#2fbc9e;
  --panel:#f1f2f5;
  --white:#ffffff;
  --ink:#2a2a2a;
  --muted:#6d7380;
  --line:#dfe3ea;
  --track:#cfe3fb;
  --tab-dark:#3a3a3a;
  --red:#db4437;
  --amber:#f4b400;
}
*{box-sizing:border-box;margin:0;padding:0}
html,body{width:1200px;height:1198px;overflow:hidden}
body{position:relative;background:var(--stage);font-family:"Montserrat",sans-serif;color:var(--ink)}
.accent-top{position:absolute;left:0;top:0;width:487px;height:347px;background:var(--brand)}
.accent-left{position:absolute;left:0;top:0;width:39px;height:447px;background:var(--brand)}
.accent-corner{position:absolute;right:0;bottom:0;width:1200px;height:1198px}

.screen{position:absolute;width:549px;background:var(--panel);box-shadow:0 2px 6px rgba(0,0,0,.18);overflow:hidden}
.steps{position:absolute;left:0;top:0;width:100%;height:36px;background:var(--white);border-bottom:1px solid var(--line)}
.step{position:absolute;top:11px;display:flex;align-items:center;gap:6px;font-size:6.8px;font-weight:500;white-space:nowrap}
.step .dot{width:13px;height:13px;border-radius:50%;border:1px solid var(--line);display:flex;align-items:center;justify-content:center;font-size:6px;color:var(--brand);background:var(--white)}
.step.current .dot{background:var(--brand);border-color:var(--brand);color:var(--white)}
.step .dot svg{width:7px;height:7px}
.s1{left:30px}.s2{left:125px}.s3{left:233px}.s4{left:341px}.s5{left:467px}
.nav-tabs{position:absolute;right:0;top:8px;display:flex;height:21px}
.nav-tab{width:9px;height:21px;writing-mode:vertical-rl;transform:rotate(180deg);font-size:5px;font-weight:600;color:var(--white);display:flex;align-items:center;justify-content:center;letter-spacing:.3px}
.nav-tab.prev{background:var(--tab-dark)}
.nav-tab.next{background:var(--brand)}

.title{position:absolute;left:0;width:100%;text-align:center;font-size:12px;font-weight:500}
.ring{position:absolute;width:124px;height:124px;border-radius:50%;border:7px solid var(--brand);background:var(--white);box-shadow:0 3px 8px rgba(0,0,0,.12);text-align:center}
.ring.teal{border-color:var(--teal)}
.ring .art{position:absolute;left:50%;transform:translateX(-50%);border-radius:8px}
.ring .label{position:absolute;left:0;width:100%;font-weight:700;color:var(--brand)}
.ring .desc{position:absolute;left:14px;right:14px;font-size:4.6px;line-height:9px;color:var(--muted)}

.field-label{position:absolute;font-size:5.6px;color:var(--muted)}
.slider{position:absolute;height:4px;border-radius:2px;background:var(--track)}
.slider .fill{position:absolute;left:0;top:0;height:4px;border-radius:2px;background:var(--brand)}
.slider .knob{position:absolute;top:-1.5px;width:7px;height:7px;border-radius:50%;background:#3b4048;border:1px solid var(--white)}
.slider-value{position:absolute;font-size:5.8px;color:var(--muted)}
.select{position:absolute;height:16px;background:var(--white);border:1px solid var(--line);font-size:4.8px;color:var(--ink);padding:0 7px;display:flex;align-items:center;justify-content:space-between;box-shadow:0 1px 2px rgba(0,0,0,.06)}
.select::after{content:"";border:2px solid transparent;border-top:2.5px solid var(--ink);margin-top:2px}
.card{position:absolute;background:var(--white);box-shadow:0 1px 3px rgba(0,0,0,.1)}
.card svg{position:absolute;left:0;top:0;width:100%;height:100%}
.result h3{position:absolute;left:25px;font-size:9px;font-weight:500}
.result p{position:absolute;left:25px;font-size:5.6px;color:var(--muted)}
.result .info{display:inline-block;width:5px;height:5px;border-radius:50%;background:var(--brand);margin-left:4px;vertical-align:middle}
.result .link{color:var(--brand);font-size:6.6px;font-weight:500}
.note{position:absolute;left:28px;top:403px;width:493px;height:19px;background:#dbe9fb;border:1px solid #c5dbf7;font-size:4px;color:#4a5566;display:flex;align-items:center;justify-content:center}
.advanced{position:absolute;left:28px;top:431px;width:493px;height:20px;background:var(--white);border:1px solid var(--line);font-size:5.4px;color:var(--muted);display:flex;align-items:center;padding-left:18px}
.map-art{position:absolute;left:76px;top:117px;width:170px;height:158px;border-radius:40% 48% 45% 38%;background:linear-gradient(100deg,var(--brand-light) 0 38%,var(--brand-deep) 38%)}
</style>
</head>
<body>
<div class="accent-top"></div>
<div class="accent-left"></div>
<svg class="accent-corner" viewBox="0 0 1200 1198"><polygon points="1200,990 1200,1198 960,1198" fill="#1a8cff"/></svg>

<!-- Step 1: property type -->
<section class="screen" style="left:38px;top:43px;height:279px">
  <header class="steps">
    <div class="step s1 current"><span class="dot">1</span>Property Type</div>
    <div class="step s2"><span class="dot">2</span>Property Location</div>
    <div class="step s3"><span class="dot">3</span>Property Valuation</div>
    <div class="step s4"><span class="dot">4</span>Your Property Forecast</div>
    <div class="step s5"><span class="dot">5</span>Calculaion</div>
    <div class="nav-tabs"><span class="nav-tab next">NEXT</span></div>
  </header>
  <h2 class="title" style="top:70px">What Type Of Property Would You Like To Compare?</h2>
  <div class="ring" style="left:135px;top:114px">
    <div class="art" role="img" aria-label="Illustration of two townhouse units" style="top:14px;width:56px;height:58px;background:linear-gradient(90deg,#f47f6b 50%,#8fc3f2 50%)"></div>
    <div class="label" style="top:83px;font-size:9.5px">UNIT</div>
  </div>
  <div class="ring teal" style="left:289px;top:114px">
    <div class="art" role="img" aria-label="Illustration of a house with the sun behind it" style="top:18px;width:62px;height:52px;background:linear-gradient(180deg,#fde3b0,#e9eef5)"></div>
    <div class="label" style="top:83px;font-size:9.5px">HOUSE</div>
  </div>
</section>

<!-- Step 2: location -->
<section class="screen" style="left:38px;top:348px;height:302px">
  <header class="steps">
    <div class="step s1"><span class="dot"><svg viewBox="0 0 10 10"><path d="M2 5.2l2 2 4-4.4" fill="none" stroke="#1a8cff" stroke-width="1.6"/></svg></span>Property Type</div>
    <div class="step s2 current"><span class="dot">2</span>Property Location</div>
    <div class="step s3"><span class="dot">3</span>Property Valuation</div>
    <div class="step s4"><span class="dot">4</span>Your Property Forecast</div>
    <div class="step s5"><span class="dot">5</span>Calculaion</div>
    <div class="nav-tabs"><span class="nav-tab prev">PREV</span><span class="nav-tab next">NEXT</span></div>
  </header>
  <h2 class="title" style="top:68px">Where Would This Property Be Located?</h2>
  <div class="map-art" role="img" aria-label="Map of Australia divided into selectable states"></div>
  <div class="field-label" style="left:272px;top:164px">How Much Will The Property Cost?</div>
  <div class="slider" style="left:272px;top:179px;width:171px"><div class="fill" style="width:45px"></div><div class="knob" style="left:42px"></div></div>
  <div class="slider-value" style="left:449px;top:177px">$500,000</div>
  <div class="field-label" style="left:272px;top:206px">How Much Will You Invest?</div>
  <div class="slider" style="left:272px;top:221px;width:171px"><div class="fill" style="width:45px"></div><div class="knob" style="left:42px"></div></div>
  <div class="slider-value" style="left:449px;top:219px">$200,000</div>
</section>

<!-- Step 5: calculation -->
<section class="screen" style="left:38px;top:673px;height:481px">
  <header class="steps">
    <div class="step s1"><span class="dot"><svg viewBox="0 0 10 10"><path d="M2 5.2l2 2 4-4.4" fill="none" stroke="#1a8cff" stroke-width="1.6"/></svg></span>Property Type</div>
    <div class="step s2"><span class="dot"><svg viewBox="0 0 10 10"><path d="M2 5.2l2 2 4-4.4" fill="none" stroke="#1a8cff" stroke-width="1.6"/></svg></span>Property Location</div>
    <div class="step s3"><span class="dot"><svg viewBox="0 0 10 10"><path d="M2 5.2l2 2 4-4.4" fill="none" stroke="#1a8cff" stroke-width="1.6"/></svg></span>Property Valuation</div>
    <div class="step s4"><span class="dot"><svg viewBox="0 0 10 10"><path d="M2 5.2l2 2 4-4.4" fill="none" stroke="#1a8cff" stroke-width="1.6"/></svg></span>Your Property Forecast</div>
    <div class="step s5 current"><span class="dot">5</span>Calculaion</div>
    <div class="nav-tabs"><span class="nav-tab prev">PREV</span><span class="nav-tab next">RECAL</span></div>
  </header>
  <h2 class="title" style="top:66px">Your Property Price Forecast</h2>
  <div class="field-label" style="left:28px;top:119px">Choose Property</div>
  <div class="select" style="left:130px;top:115px;width:95px">Sydney House</div>
  <div class="field-label" style="left:28px;top:143px">Choose Alternative Invesement</div>
  <div class="select" style="left:130px;top:139px;width:95px">Global Shares</div>
  <div class="field-label" style="left:28px;top:170px">How Much Will The Property Cost?</div>
  <div class="slider" style="left:29px;top:186px;width:167px"><div class="fill" style="width:44px"></div><div class="knob" style="left:41px"></div></div>
  <div class="slider-value" style="left:203px;top:184px">$500,000</div>
  <div class="field-label" style="left:28px;top:212px">How Much Will You Invest?</div>
  <div class="slider" style="left:29px;top:228px;width:167px"><div class="fill" style="width:44px"></div><div class="knob" style="left:41px"></div></div>
  <div class="slider-value" style="left:203px;top:226px">$200,000</div>

  <div class="card" style="left:278px;top:115px;width:242px;height:117px">
    <svg viewBox="0 0 242 117" font-family="Montserrat,sans-serif" font-size="3.2" fill="#666">
      <text x="92" y="6">Day</text>
      <text x="21" y="15">0</text><text x="69" y="15">5</text><text x="117" y="15">10</text><text x="166" y="15">15</text>
      <g stroke="#e6e6e6" stroke-width=".4">
        <line x1="18" y1="18" x2="171" y2="18"/><line x1="18" y1="37" x2="171" y2="37"/><line x1="18" y1="55" x2="171" y2="55"/><line x1="18" y1="74" x2="171" y2="74"/><line x1="18" y1="92" x2="171" y2="92"/><line x1="18" y1="110" x2="171" y2="110"/>
      </g>
      <text x="12" y="19">100</text><text x="13" y="38">80</text><text x="13" y="56">60</text><text x="13" y="75">40</text><text x="13" y="93">20</text><text x="15" y="111">0</text>
      <polyline points="32,36 42,46 51,56 60,92 70,93 79,97 89,98 98,84 108,74 117,84 127,103 136,102 146,104 156,104" fill="none" stroke="#db4437" stroke-width=".8"/>
      <polyline points="32,72 42,79 51,85 60,101 70,102 79,104 89,103 98,98 108,96 117,99 127,106 136,105 146,107 156,107" fill="none" stroke="#f4b400" stroke-width=".8"/>
      <polyline points="32,74 42,80 51,85 60,102 70,103 79,105 89,102 98,96 108,94 117,98 127,105 136,104 146,106 156,106" fill="none" stroke="#4285f4" stroke-width=".8"/>
      <rect x="183" y="44" width="3" height="3" fill="#db4437"/><text x="189" y="47">Shares</text>
      <rect x="183" y="55" width="3" height="3" fill="#f4b400"/><text x="189" y="58">Property</text>
      <rect x="183" y="66" width="3" height="3" fill="#4285f4"/><text x="189" y="69">Property if no Debt</text>
    </svg>
  </div>

  <div class="card" style="left:28px;top:262px;width:242px;height:118px">
    <svg viewBox="0 0 242 118" font-family="Montserrat,sans-serif" font-size="3.2" fill="#666">
      <g stroke="#e6e6e6" stroke-width=".4">
        <line x1="16" y1="16" x2="175" y2="16"/><line x1="16" y1="37" x2="175" y2="37"/><line x1="16" y1="58" x2="175" y2="58"/><line x1="16" y1="79" x2="175" y2="79"/><line x1="16" y1="100" x2="175" y2="100"/>
      </g>
      <line x1="16" y1="100" x2="175" y2="100" stroke="#999" stroke-width=".5"/>
      <text x="10" y="17">80</text><text x="10" y="38">60</text><text x="10" y="59">40</text><text x="10" y="80">20</text><text x="12" y="101">0</text>
      <g stroke="#3264c8" stroke-width=".6">
        <line x1="34" y1="52" x2="34" y2="78"/><line x1="65" y1="30" x2="65" y2="66"/><line x1="96" y1="16" x2="96" y2="46"/><line x1="127" y1="18" x2="127" y2="47"/><line x1="158" y1="28" x2="158" y2="83"/>
      </g>
      <rect x="24" y="59" width="19" height="10" fill="#3264c8"/>
      <rect x="55" y="41" width="19" height="17" fill="#3264c8"/>
      <rect x="86" y="19" width="19" height="22" fill="#3264c8"/>
      <rect x="117" y="20" width="19" height="10" fill="#fff" stroke="#3264c8" stroke-width=".6"/>
      <rect x="148" y="30" width="19" height="45" fill="#fff" stroke="#3264c8" stroke-width=".6"/>
      <text x="31" y="105">Mon</text><text x="62" y="105">Tue</text><text x="92" y="105">Wed</text><text x="124" y="105">Thu</text><text x="156" y="105">Fri</text>
      <rect x="182" y="39" width="3" height="3" fill="#3264c8"/><text x="188" y="42">Shares Cashflow</text>
      <rect x="182" y="50" width="3" height="3" fill="#fff" stroke="#3264c8" stroke-width=".5"/><text x="188" y="53">Property Cashflow</text>
    </svg>
  </div>

  <div class="card result" style="left:278px;top:262px;width:242px;height:118px">
    <h3 style="top:16px">After 5 Years:</h3>
    <p style="top:37px">Shares Will Return $832,431 More<span class="info"></span></p>
    <h3 style="top:56px">After 10 Years:</h3>
    <p style="top:77px">Shares Will Return $160,176 More<span class="info"></span></p>
    <p class="link" style="top:93px">Debt Contribution<span class="info"></span></p>
  </div>

  <div class="note">Note : These are Indicative Figures On A Broad Range of Assumptions(below).Please Contact Larkhollow Funds Or A Financial Planner Before Making Any Invesement Based On The Assumption From This Calculator.</div>
  <div class="advanced">›&nbsp;&nbsp;Advanced Options</div>
</section>

<!-- Step 3: valuation -->
<section class="screen" style="left:612px;top:43px;height:302px">
  <header class="steps">
    <div class="step s1"><span class="dot"><svg viewBox="0 0 10 10"><path d="M2 5.2l2 2 4-4.4" fill="none" stroke="#1a8cff" stroke-width="1.6"/></svg></span>Property Type</div>
    <div class="step s2"><span class="dot"><svg viewBox="0 0 10 10"><path d="M2 5.2l2 2 4-4.4" fill="none" stroke="#1a8cff" stroke-width="1.6"/></svg></span>Property Location</div>
    <div class="step s3 current"><span class="dot">3</span>Property Valuation</div>
    <div class="step s4"><span class="dot">4</span>Your Property Forecast</div>
    <div class="step s5"><span class="dot">5</span>Calculaion</div>
    <div class="nav-tabs"><span class="nav-tab prev">PREV</span><span class="nav-tab next">NEXT</span></div>
  </header>
  <h2 class="title" style="top:74px">How Would you Like To Forecast The Returns From Property?</h2>
  <div class="ring" style="left:54px;top:119px">
    <div class="art" role="img" aria-label="Money bag with stacked coins" style="top:12px;width:38px;height:38px;background:linear-gradient(135deg,#f25a5a,#f6c744)"></div>
    <div class="label" style="top:62px;font-size:7.6px">Relative Cost</div>
    <div class="desc" style="top:74px">Use This To value Property Based On Mortgage Cost Relative To Rent Cost</div>
  </div>
  <div class="ring teal" style="left:213px;top:119px">
    <div class="art" role="img" aria-label="Gold coin dropping into a hand" style="top:12px;width:38px;height:38px;background:linear-gradient(180deg,#f6c744,#6b7fa8)"></div>
    <div class="label" style="top:62px;font-size:7.6px">Relative To Wages</div>
    <div class="desc" style="top:74px">Use This To value Property Based On Mortgage Cost Relative To Wages</div>
  </div>
  <div class="ring" style="left:371px;top:119px">
    <div class="art" role="img" aria-label="Rent sign on a house badge" style="top:12px;width:38px;height:38px;border-radius:50%;background:#f25a5a"></div>
    <div class="label" style="top:62px;font-size:7.6px">Using Rental Yield</div>
    <div class="desc" style="top:74px">Use This To value Property Based On Rental Yield</div>
  </div>
</section>

<!-- Step 4: forecast -->
<section class="screen" style="left:612px;top:369px;height:399px">
  <header class="steps">
    <div class="step s1"><span class="dot"><svg viewBox="0 0 10 10"><path d="M2 5.2l2 2 4-4.4" fill="none" stroke="#1a8cff" stroke-width="1.6"/></svg></span>Property Type</div>
    <div class="step s2"><span class="dot"><svg viewBox="0 0 10 10"><path d="M2 5.2l2 2 4-4.4" fill="none" stroke="#1a8cff" stroke-width="1.6"/></svg></span>Property Location</div>
    <div class="step s3"><span class="dot"><svg viewBox="0 0 10 10"><path d="M2 5.2l2 2 4-4.4" fill="none" stroke="#1a8cff" stroke-width="1.6"/></svg></span>Property Valuation</div>
    <div class="step s4 current"><span class="dot">4</span>Your Property Forecast</div>
    <div class="step s5"><span class="dot">5</span>Calculaion</div>
    <div class="nav-tabs"><span class="nav-tab prev">PREV</span><span class="nav-tab next">NEXT</span></div>
  </header>
  <h2 class="title" style="top:68px">Your Property Price Forecast</h2>
  <div class="field-label" style="right:251px;top:108px">You Have Chosen To Forecast Property Prices Using</div>
  <div class="select" style="left:306px;top:103px;width:96px">Gross Rental Yield</div>
  <div class="field-label" style="right:174px;top:141px">You can See How This Ratio Has Changed Over Time (in blue)Below Vs Your Assumption (in Red) For</div>
  <div class="select" style="left:384px;top:136px;width:95px">Sydney House</div>
  <div class="card" style="left:138px;top:182px;width:273px;height:119px">
    <svg viewBox="0 0 273 119" font-family="Montserrat,sans-serif" font-size="4" fill="#555">
      <g stroke="#e6e6e6" stroke-width=".4">
        <line x1="44" y1="27" x2="227" y2="27"/><line x1="44" y1="44" x2="227" y2="44"/><line x1="44" y1="61" x2="227" y2="61"/><line x1="44" y1="78" x2="227" y2="78"/>
        <line x1="97" y1="27" x2="97" y2="94"/><line x1="150" y1="27" x2="150" y2="94"/><line x1="203" y1="27" x2="203" y2="94"/>
      </g>
      <line x1="44" y1="94" x2="227" y2="94" stroke="#555" stroke-width=".5"/>
      <line x1="44" y1="27" x2="44" y2="94" stroke="#555" stroke-width=".5"/>
      <text x="34" y="28">80</text><text x="34" y="45">60</text><text x="34" y="62">40</text><text x="34" y="79">20</text><text x="37" y="96">0</text>
      <text x="43" y="102">0</text><text x="95" y="102">20</text><text x="148" y="102">40</text><text x="201" y="102">60</text>
      <text x="130" y="112" font-style="italic">Time</text>
      <text x="20" y="70" transform="rotate(-90 20 70)" font-style="italic">Popularity</text>
      <polyline points="44,93 47,85 49,74 52,81 54,80 56,85 59,71 61,67 65,60 67,64 70,57 72,62 75,55 78,56 81,50 84,47 86,53 88,50 91,49 93,44 96,45 98,49 101,46 104,47 107,46 110,47 113,43 116,46 119,41 122,40 124,43 127,37 130,41 134,43 137,42 141,38 144,41 147,39 150,37 154,38 157,36 160,36 164,37 168,35 172,34 175,35 178,33 182,32 185,38 187,35 190,39 193,36 197,34 200,33 203,33 207,31 210,30 213,27 216,26 219,28 222,27 224,25 227,22" fill="none" stroke="#3264c8" stroke-width=".7"/>
      <line x1="232" y1="29" x2="241" y2="29" stroke="#3264c8" stroke-width=".7"/><text x="243" y="30.5">Dogs</text>
    </svg>
  </div>
  <div class="field-label" style="left:0;width:100%;text-align:center;top:335px;font-size:5.2px">By Default We Assume The Ratio Stays at The Latest Value of 3.4%.You Can Charge This Assuption Using The Slider.</div>
  <div class="slider" style="left:116px;top:354px;width:317px"><div class="fill" style="width:45px"></div><div class="knob" style="left:42px"></div></div>
  <div class="slider-value" style="left:292px;top:366px;font-size:5.2px">3.4%</div>
</section>
</body>
</html>
```